banner for website

I need a new banner for my website. My website now is. www.brightmeadowkitchen.com, but I'm changing it to Bright Meadow Table and I need a new banner. I want me to be who it's about. I am my brand. I'm Carla Whitford. So, my name needs to be prominent in the banner along with my photo, which I'm attaching. I want my photo very prominent in the banner and very large. I am attaching my two favorites.
I need the banner plain ( with out the newsletter sign up optin part), so I can use it on my newsletters, emails and letter head, as well. I would like it to be inviting. I I have a certain color scheme I use. Deep dark brown letters with blues and greens. Very earthy and psychologically grounded. I would like to keep that color scheme. In my website banner, I need a opt in to sign up for my free monthly newsletter and receive my Free Pantry Basket Planner.

I want the shopping guide to be small and pleasant looking and to say: "Sign up to receive your Free Pantry Basket Planner and monthly newsletter."

I only want my banner to say: "Bright Meadow Table" "Carla Whitford"

I would also like to have part of the banner without the sign in for the newsletter part off of it. And also one with only the "Bright Meadow Table" and one with "Bright Meadow Table" and "Carla Whitford" without the newsletter sign up part on it either.

I hope you can do this for me. I look forward to seeing your design! Sincerely, Carla
Updates

Project Deadline Extended Reason: I couldn't view the designs so I couldn't look at the ones submitted. I just now got into the website with your company's help. I don't want to be penalized because of a problem with the log in at your site. That was not my fault. Please let me know your thoughts. Added Monday, May 9, 2016

Target Market(s)

people over 40 who have bad health or who want to learn how to be a vegetarian for better health.

Number of Pages Required

1 page

Requirements
Must have
• I want the shopping guide to be small and pleasant looking and to say: "Sign up to receive your Free Pantry Basket Planner and monthly newsletter." I would like it to blend and be elegant and not in the middle of the banner or across my face.
• I only want my banner to say: "Bright Meadow Table" "Carla Whitford"
• I would also like to have part of the banner without the sign in for the newsletter part off of it. And also one with only the "Bright Meadow Table" and one with "Bright Meadow Table" and "Carla Whitford" without the newsletter sign up part on it either.
Nice to have
• Nice font and colors. I want the background to be plants and earthy and inviting.
Should not have
• I updated and added two new photos. I think the one you were using with me in the red top looked funny under my eyes. it was too pink or something. I uploaded a better version of that photo. in hopes that it looks better. Please switch those out if you are using the one with me in the red top.

```html
<!DOCTYPE html>
<html lang="en">
<head>
<meta charset="utf-8">
<title>Bright Meadow Table — Carla Whitford</title>
<link rel="stylesheet" href="https://fonts.googleapis.com/css2?family=Oswald:wght@500;600&family=Roboto:wght@400;700&family=Yellowtail&family=Noto+Serif:ital,wght@0,400;0,600;1,400&family=Noto+Sans:wght@400&family=Merriweather:wght@300&family=Raleway:wght@400&display=swap">
<style>
  :root {
    --leaf-light: #cfe3a0;
    --leaf-mid: #86b04a;
    --leaf-deep: #3f6a24;
    --bark: #4a3d30;
    --ink: #333333;
    --ink-soft: #555555;
    --title: #5a5a5a;
    --sun: #f6e51c;
    --white: #ffffff;
    --accent: #e07a2a;
    --link: #3c7a18;
    --button-top: #3aa01e;
    --button-bottom: #1f6f0c;
    --field-text: #888888;
  }
  * { box-sizing: border-box; margin: 0; padding: 0; }
  html, body { width: 1200px; height: 556px; overflow: hidden; background: var(--white); }
  body { position: relative; font-family: "Noto Sans", sans-serif; }

  .hero {
    position: absolute; left: 0; top: 0; width: 1200px; height: 239px;
    background:
      linear-gradient(90deg, rgba(0,0,0,0) 60%, rgba(30,40,20,0.25) 75%, rgba(30,40,20,0.15) 100%),
      radial-gradient(ellipse 170px 230px at 530px 110px, #e8d3b4 0%, #d8c090 40%, rgba(216,192,144,0) 75%),
      radial-gradient(ellipse 300px 200px at 1060px 150px, #6a7d34 0%, #4f6a26 45%, rgba(79,106,38,0) 80%),
      linear-gradient(90deg, #9dc46a 0%, #d9ebb2 22%, #eef5d6 38%, #cfe0a0 55%, #5f7f2c 72%, #3f5e1e 100%);
  }
  .hero-photo { position: absolute; inset: 0; }

  .brand {
    position: absolute; left: 140px; top: 44px;
    display: flex; align-items: center; gap: 10px;
  }
  .brand-dot { width: 36px; height: 36px; border-radius: 50%; background: var(--leaf-deep); }
  .brand-name {
    font-family: "Raleway", sans-serif; font-weight: 400; font-size: 24px; line-height: 25px;
    color: var(--leaf-deep);
  }
  .signature {
    position: absolute; left: 180px; top: 122px;
    font-family: "Yellowtail", cursive; font-size: 48px; color: var(--ink);
  }

  .optin { position: absolute; left: 703px; top: 28px; width: 380px; }
  .optin-lead { display: flex; align-items: flex-end; gap: 6px; }
  .optin-signup {
    font-family: "Oswald", sans-serif; font-weight: 600; font-size: 38px; line-height: 40px;
    color: var(--sun);
  }
  .optin-note {
    font-family: "Roboto", sans-serif; font-weight: 700; font-size: 16px; line-height: 17px;
    color: var(--sun); padding-bottom: 3px;
  }
  .optin-offer {
    margin-top: 10px;
    font-family: "Oswald", sans-serif; font-weight: 500; color: var(--white);
    letter-spacing: -0.3px;
  }
  .optin-offer .line-one { display: block; font-size: 23px; line-height: 24px; }
  .optin-offer .line-two { display: block; font-size: 31px; line-height: 32px; }
  .optin-form {
    position: absolute; left: 0; top: 119px;
    display: grid; grid-template-columns: 179px 179px; gap: 12px 8px;
  }
  .field {
    height: 28px; border-radius: 14px; background: var(--white); border: none;
    padding-left: 18px; font-family: "Roboto", sans-serif; font-size: 12px; color: var(--field-text);
    display: flex; align-items: center;
  }
  .signup-button {
    height: 28px; border-radius: 14px; border: 2px solid var(--white);
    background: linear-gradient(var(--button-top), var(--button-bottom));
    color: var(--white); font-family: "Roboto", sans-serif; font-weight: 700; font-size: 15px;
    display: flex; align-items: center; justify-content: center;
  }

  .site-nav {
    position: absolute; left: 0; top: 239px; width: 1200px; height: 53px;
    background: var(--bark);
    box-shadow: 0 6px 10px rgba(0,0,0,0.12);
  }
  .nav-list { position: absolute; left: 139px; top: 4px; display: flex; list-style: none; }
  .nav-item {
    height: 49px; padding: 0 13px; display: flex; align-items: center;
    font-family: "Noto Serif", serif; font-weight: 600; font-size: 14px; color: var(--white);
  }
  .nav-item.is-current { background: var(--white); color: var(--accent); border-radius: 3px 3px 0 0; font-weight: 400; }

  .services { position: absolute; left: 149px; top: 334px; display: flex; }
  .service { display: flex; width: 320px; }
  .service-media { width: 100px; height: 100px; flex: none; }
  .service-media.talk { background: linear-gradient(135deg, #8a8a8a, #c9c9c9 45%, #6b6b6b); }
  .service-media.counsel {
    width: 92px; height: 84px; margin: 2px 0 0 4px; border: 4px solid var(--white);
    box-shadow: 0 1px 4px rgba(0,0,0,0.35); transform: rotate(-3deg);
    background: linear-gradient(135deg, #d9a6c4, #b58a7a 55%, #e6c6d8);
  }
  .service-media.books {
    width: 96px; height: 96px; transform: rotate(-6deg);
    background: linear-gradient(135deg, #2f3b22, #5b7a34 50%, #e9e2d0);
    box-shadow: 3px 3px 5px rgba(0,0,0,0.3);
  }
  .service-body { margin-left: 25px; width: 175px; }
  .service-title {
    font-family: "Merriweather", serif; font-weight: 300; font-size: 21px; line-height: 24px;
    color: var(--title);
  }
  .service-text {
    margin-top: 13px; font-size: 13.5px; line-height: 20px; color: var(--ink-soft);
  }
  .service-link {
    display: block; margin-top: 8px;
    font-family: "Noto Serif", serif; font-style: italic; font-size: 15.5px; color: var(--link);
    text-decoration: none;
  }
</style>
</head>
<body>
  <header class="hero">
    <div class="hero-photo" role="img" aria-label="Sunlit green garden foliage with a portrait of Carla smiling in the centre and fresh vegetables on the right"></div>

    <div class="brand">
      <span class="brand-dot"></span>
      <span class="brand-name">Bright Meadow<br>Table</span>
    </div>
    <div class="signature">Carla Whitford</div>

    <section class="optin">
      <div class="optin-lead">
        <span class="optin-signup">SIGN UP</span>
        <span class="optin-note">to receive Carla's monthly<br>newsletter and receive here...</span>
      </div>
      <p class="optin-offer">
        <span class="line-one">COMPLIMENTARY HEALTHY</span>
        <span class="line-two">PANTRY BASKET PLANNER!</span>
      </p>
      <div class="optin-form">
        <div class="field">First Name</div>
        <div class="field">Last Name</div>
        <div class="field">Email</div>
        <div class="signup-button">SIGN UP</div>
      </div>
    </section>
  </header>

  <nav class="site-nav">
    <ul class="nav-list">
      <li class="nav-item is-current">Home</li>
      <li class="nav-item">Speaking&nbsp;»</li>
      <li class="nav-item">Counseling&nbsp;»</li>
      <li class="nav-item">Retreats &amp; Classes</li>
      <li class="nav-item">Meet Carla&nbsp;»</li>
      <li class="nav-item">Store&nbsp;»</li>
      <li class="nav-item">Blog</li>
      <li class="nav-item">References</li>
      <li class="nav-item">Media</li>
    </ul>
  </nav>

  <main class="services">
    <article class="service">
      <div class="service-media talk" role="img" aria-label="Carla speaking on stage in front of a presentation screen"></div>
      <div class="service-body">
        <h2 class="service-title">Motivational Speaker</h2>
        <p class="service-text">Carla is a member of the Guild of Wellness Speakers, traveling internationally, employee wellness programs and ...</p>
        <a class="service-link" href="#">Learn more</a>
      </div>
    </article>
    <article class="service">
      <div class="service-media counsel" role="img" aria-label="Framed portrait of Carla among blossoms with a microphone"></div>
      <div class="service-body">
        <h2 class="service-title">Nutrition Counseling</h2>
        <p class="service-text">Whether you are looking for individualized personal health &amp; nutrition counseling, family coaching, cooking classes or a private...</p>
        <a class="service-link" href="#">Learn more</a>
      </div>
    </article>
    <article class="service">
      <div class="service-media books" role="img" aria-label="Stack of Carla's nutrition books and DVDs"></div>
      <div class="service-body">
        <h2 class="service-title">Best Nutrition, Books &amp; Products</h2>
        <p class="service-text">Books &amp; DVD’s on nutrition &amp; healthy recipes. Food, Body Care, &amp; Home Products. Find it all here.</p>
        <a class="service-link" href="#">Learn more</a>
      </div>
    </article>
  </main>
</body>
</html>
```